New Company Logo & Responsive Website Design for Codeworks Heron

Codeworks Heron provides a white labeled, digital lending platform technology solutions to the mortgage industry via a SaaS model. Our target market is Mortgage Companies and Banks who are looking for innovative technology to assist both borrowers and loan originators with the lending process, while automating as much of he process as possible.

Codeworks Heron is our company name, and our modular software offerings Include the following Products:

1) Applicant Heron: A customizable, web based, point-of-sale application for borrowers to complete a loan application, and guide them through the mortgage process.

POS Definition
"A point of sale (POS) is the client-facing software solution that allows borrowers to create a customer portal, apply for a loan online, and seamlessly submit needed documentation."

2) Ledger Heron: A Mortgage Loan Origination System

LOS Definition
"A Mortgage Loan Origination System (LOS) is a platform that takes a completed loan application and facilitates the mortgage transaction from origination to post closing. LOS systems may include document management, pricing and eligibility engines, and compliance tools to decrease risk and increase loan manufacturing quality.

3) Dwelling Heron: A brandable, home search website

The LOS and POS definitions provided above are just for your understanding of what these products are, not to be included word-for-word as website content.

We are looking for designs that are elegant, convey technical competency, simple to navigate, and set us apart from the competition.

We are not set on any particular colors at this point, so feel free to choose the best colors for your particular designs.

Please include company logo, both desktop and mobile designs with a template design for the website sub pages.

Some Examples of Mortgage Technology Websites offering similar products. These are to show the typical content, not designs that we particularly like or dislike.

https://brantiq.example/
https://www.clearvantro.example/
https://www.abodefundbuddy.example/
https://www.debtquokka.example/
https://www.ternixapps.example/products/trail

Please send comments with additional questions.

Thank You For your participation.

Mortgage Companies

```html
<!DOCTYPE html>
<html lang="en">
<head>
<meta charset="utf-8">
<title>Codeworks Heron – Digital Lending Platform Technology</title>
<link rel="stylesheet" href="https://fonts.googleapis.com/css2?family=Playfair+Display:wght@700&family=Montserrat:wght@500;600;700&family=Mulish:wght@400;600;700&display=swap">
<style>
:root{
  --blue:#1f63bd;
  --orange:#f37021;
  --ink:#1c1c1c;
  --text:#444;
  --muted:#f3f3f5;
  --panel:#ebebee;
  --footer:#232125;
  --white:#fff;
}
*{box-sizing:border-box;margin:0;padding:0}
html,body{width:1200px;height:4187px;overflow:hidden}
body{font-family:"Mulish",sans-serif;color:var(--text);background:var(--white);position:relative}
.abs{position:absolute}
.btn{position:absolute;display:flex;align-items:center;justify-content:center;background:var(--orange);color:var(--white);font-family:"Montserrat",sans-serif;font-weight:700;text-transform:uppercase;letter-spacing:.3px;text-decoration:none}
.wordmark{position:absolute;font-family:"Montserrat",sans-serif;font-weight:700;white-space:nowrap;letter-spacing:0}
.rule{position:absolute;height:3px;width:44px;background:var(--blue)}
.section-title{position:absolute;left:0;width:1200px;text-align:center;font-family:"Montserrat",sans-serif;font-weight:600;font-size:24px;color:var(--ink)}
.photo{position:absolute}

/* header */
.site-header{position:absolute;left:0;top:0;width:1200px;height:72px;background:var(--white)}
.site-header .wordmark{left:130px;top:21px;font-size:24px;color:var(--ink)}
.nav-link{position:absolute;top:26px;font-size:14px;color:var(--ink);text-decoration:none}
.nav-link.active{color:var(--orange);border-bottom:1px solid var(--orange)}
/* hero */
.hero{position:absolute;left:0;top:72px;width:1200px;height:502px;background:linear-gradient(120deg,#2a6fc8 0%,#1f5fb8 50%,#2b73cc 100%)}
.hero-title{position:absolute;left:0;top:130px;width:1200px;text-align:center;font-family:"Playfair Display",serif;font-weight:700;font-size:44px;color:var(--white)}
.hero-sub{position:absolute;left:0;top:200px;width:1200px;text-align:center;font-family:"Montserrat",sans-serif;font-weight:500;font-size:18.5px;line-height:26px;color:var(--white)}
.dots{position:absolute;left:0;width:1200px;display:flex;justify-content:center;gap:6px}
.dots span{width:11px;height:11px;border-radius:50%;border:1.5px solid var(--white)}
.dots .on{background:var(--orange);border-color:var(--orange)}
/* intro */
.intro-title{left:130px;top:636px;font-family:"Montserrat",sans-serif;font-weight:600;font-size:24px;line-height:34px;color:var(--ink)}
.intro-text{left:130px;top:756px;width:378px;font-size:14px;line-height:20.2px;color:var(--text)}
/* products */
.products{position:absolute;left:0;top:1085px;width:1200px;height:1414px;background:var(--muted)}
.prod-title{position:absolute;font-family:"Montserrat",sans-serif;font-weight:600;font-size:19px;color:var(--ink)}
.prod-text{position:absolute;font-size:14px;line-height:24px;color:var(--text)}
.def-box{position:absolute;background:var(--panel);padding:26px 34px}
.def-box h4{font-family:"Montserrat",sans-serif;font-weight:500;font-size:12.5px;color:var(--ink);margin-bottom:10px}
.def-box p{font-size:12.3px;line-height:17.6px;color:var(--text)}
.icon-card{position:absolute;width:73px;height:82px;background:var(--white);border-radius:4px;box-shadow:0 4px 12px rgba(0,0,0,.14);display:flex;flex-direction:column;align-items:center;justify-content:center;gap:6px;font-size:10px;color:#333}
/* testimonials */
.testimonials{position:absolute;left:0;top:2499px;width:1200px;height:506px;background:var(--blue)}
.quote-text{position:absolute;left:260px;top:187px;width:680px;text-align:center;font-size:19.5px;line-height:29px;color:var(--white)}
/* blog */
.blog-card{position:absolute;top:3138px;width:301px;height:413px;background:var(--muted)}
.blog-card .photo{left:0;top:0;width:301px;height:176px}
.blog-date{position:absolute;left:29px;top:202px;font-size:11.5px;color:#333}
.blog-title{position:absolute;left:29px;top:222px;width:250px;font-family:"Montserrat",sans-serif;font-weight:600;font-size:13.5px;line-height:18px;color:var(--ink)}
.blog-text{position:absolute;left:29px;top:274px;width:235px;font-size:11px;line-height:16px;color:var(--text)}
.blog-card .btn{left:29px;top:358px;width:76px;height:26px;font-size:8.5px}
/* cta */
.cta{position:absolute;left:0;top:3597px;width:1200px;height:297px;background:linear-gradient(100deg,#2a6cc6,#1f5fb8 60%,#2769c2)}
/* footer */
.site-footer{position:absolute;left:0;top:3894px;width:1200px;height:293px;background:var(--footer);color:var(--white)}
.foot-col{position:absolute;top:46px}
.foot-col h5{font-family:"Montserrat",sans-serif;font-weight:700;font-size:12.5px;margin-bottom:14px;letter-spacing:.2px}
.foot-col a{display:block;color:#e6e6e6;text-decoration:none;font-size:12.5px;line-height:24.5px}
.social{position:absolute;top:126px;left:918px;display:flex;gap:11px}
.social span{width:22px;height:22px;border-radius:50%;background:var(--white)}
</style>
</head>
<body>

<header class="site-header">
  <div class="wordmark">Codeworks Heron</div>
  <nav>
    <a class="nav-link active" style="left:391px">Home</a>
    <a class="nav-link" style="left:456px">About us</a>
    <a class="nav-link" style="left:544px">Products</a>
    <a class="nav-link" style="left:628px">Features</a>
    <a class="nav-link" style="left:717px">Resources</a>
    <a class="nav-link" style="left:814px">Contact us</a>
  </nav>
  <a class="btn" style="left:927px;top:19px;width:141px;height:33px;font-size:13px;text-transform:none">Schedule Demo</a>
</header>

<section class="hero" role="img" aria-label="Blue-tinted photo of hands typing on a laptop">
  <h1 class="hero-title">Digital Lending Platform Technology</h1>
  <p class="hero-sub">There are many variations of passages of Lorem Ipsum<br>availablebut the majority have suffered alteration</p>
  <a class="btn" style="left:525px;top:282px;width:148px;height:41px;font-size:14px">Get Started</a>
  <div class="dots" style="top:440px"><span></span><span class="on"></span><span></span><span></span></div>
</section>

<section class="intro">
  <h2 class="intro-title abs">Intelligent Mortgage<br>Advisor</h2>
  <div class="rule" style="left:130px;top:721px"></div>
  <p class="intro-text abs">But I must explain to you how all this mistaken idea of denouncing pleasure and praising pain was born and I will give you a complete account of the system, and expound the actual teachings of the great explorer of the truth, the master-builder of human happiness. No one rejects, dislikes, or avoids pleasure itself, because it is pleasure, but because those who do not know how to pursue pleasure rationally encounter consequences that are extremely painful.</p>
  <a class="btn" style="left:130px;top:971px;width:119px;height:38px;font-size:12px">Read More</a>
  <div class="photo" style="left:571px;top:620px;width:497px;height:408px;background:linear-gradient(180deg,#d9dcdf 0%,#b8b4ad 55%,#6f6a66 100%)" role="img" aria-label="Photo of three colleagues meeting around a laptop in a bright office"></div>
</section>

<section class="products">
  <h2 class="section-title" style="top:36px">Our Products</h2>
  <div class="rule" style="left:578px;top:82px"></div>

  <div class="photo" style="left:130px;top:133px;width:480px;height:379px;background:linear-gradient(180deg,#8a7f78 0%,#4e5258 55%,#1e1f22 100%)" role="img" aria-label="Photo of a point-of-sale touchscreen terminal in a store"></div>
  <div class="icon-card" style="left:548px;top:435px">
    <svg width="34" height="30" viewBox="0 0 34 30" fill="none" stroke="#1f63bd" stroke-width="2"><rect x="4" y="12" width="26" height="16" rx="1"/><rect x="8" y="2" width="18" height="8"/><line x1="9" y1="17" x2="25" y2="17"/><line x1="9" y1="22" x2="25" y2="22"/></svg>
    POS
  </div>
  <h3 class="prod-title" style="left:665px;top:168px">Applicant Heron</h3>
  <p class="prod-text" style="left:666px;top:213px;width:385px">A customizable, web based, point-of-sale application for borrowers to complete a loan application, and guide them through the mortgage process.</p>
  <div class="def-box" style="left:665px;top:313px;width:395px;height:152px">
    <h4>POS Definition</h4>
    <p>A point of sale (POS) is the client-facing software solution that allows borrowers to create a customer portal, apply for a loan online, and seamlessly submit needed documentation</p>
  </div>

  <div class="photo" style="left:590px;top:559px;width:478px;height:379px;background:linear-gradient(135deg,#dfe6ee 0%,#b7c2cf 50%,#6c7785 100%)" role="img" aria-label="Photo of a hand holding a phone showing a credit score above a laptop"></div>
  <h3 class="prod-title" style="left:133px;top:630px">Ledger Heron</h3>
  <p class="prod-text" style="left:135px;top:664px;font-size:13.5px">A Mortgage Loan Origination System</p>
  <div class="def-box" style="left:133px;top:712px;width:395px;height:179px">
    <h4>LOS Definition</h4>
    <p>A Mortgage Loan Origination System (LOS) is a platform that takes a completed loan application and facilitates the mortgage transaction from origination to post closing. LOS systems may include document management, pricing and eligibility engines, and compliance tools to decrease risk and increase loan manufacturing quality</p>
  </div>
  <div class="icon-card" style="left:548px;top:861px">
    <svg width="32" height="30" viewBox="0 0 32 30" fill="none" stroke="#1f63bd" stroke-width="2"><path d="M3 14 L16 3 L29 14"/><path d="M7 11 V27 H25 V11"/><text x="16" y="23" font-size="10" text-anchor="middle" fill="#1f63bd" stroke="none" font-family="Mulish,sans-serif">%</text></svg>
    Mortgage
  </div>

  <div class="photo" style="left:130px;top:982px;width:480px;height:379px;background:linear-gradient(135deg,#d8c7a8 0%,#a89173 55%,#6e5c46 100%)" role="img" aria-label="Photo of hands on a laptop with a small wooden house model behind"></div>
  <div class="icon-card" style="left:548px;top:1284px">
    <svg width="32" height="32" viewBox="0 0 32 32" fill="none" stroke="#1f63bd" stroke-width="2"><circle cx="13" cy="13" r="10"/><line x1="20" y1="20" x2="29" y2="29"/><path d="M8 14 L13 9 L18 14 M10 12 V18 H16 V12"/></svg>
    Search Home
  </div>
  <h3 class="prod-title" style="left:665px;top:1063px">Dwelling Heron</h3>
  <p class="prod-text" style="left:666px;top:1108px;width:318px">At vero eos et accusamus et iusto odio dignissimos ducimus qui blanditiis praesentium voluptatum deleniti atque corrupti quos dolores et quas molestias excepturi sint occaecati cupiditate non provident, similique sunt in culpa qui officia deserunt mollitia animi, id est laborum et dolorum</p>
</section>

<section class="testimonials">
  <h2 class="section-title" style="top:42px;color:var(--white)">Testimonials</h2>
  <div class="rule" style="left:578px;top:89px;background:var(--white)"></div>
  <div class="abs" style="left:0;top:120px;width:1200px;text-align:center;font-family:'Playfair Display',serif;font-weight:700;font-size:40px;line-height:40px;color:var(--white)">&ldquo;</div>
  <p class="quote-text">On the other hand, we denounce with righteous indignation and dislike men who are so beguiled and demoralized by the charms of pleasure of the moment, so blinded by desire, that they cannot foresee the pain and trouble that are bound to ensue; and equal blame belongs to those who fail in their duty through weakness of will, which is the same as saying through shrinking from toil and pain. These cases are perfectly simple</p>
  <div class="abs" style="left:0;top:390px;width:1200px;text-align:center;font-family:'Montserrat',sans-serif;font-weight:700;font-size:13.5px;color:var(--white)">TOBIAS</div>
  <div class="dots" style="top:451px"><span></span><span class="on"></span><span></span><span></span></div>
</section>

<section class="blog">
  <h2 class="section-title" style="top:3044px">Latest Blog</h2>
  <div class="rule" style="left:578px;top:3095px"></div>

  <article class="blog-card" style="left:130px">
    <div class="photo" style="background:linear-gradient(135deg,#e9eef3,#9aa7b4)" role="img" aria-label="Photo of hands typing on a laptop at a white desk"></div>
    <div class="blog-date">Sep 15, 2022</div>
    <h3 class="blog-title">Sed ut perspiciatis unde omnis iste natus error</h3>
    <p class="blog-text">At vero eos et accusamus et iusto odio dignissimos ducimus qui blanditiis praes entium voluptatum deleniti atque corrupti quos dolores et quas molestias</p>
    <a class="btn">Read More</a>
  </article>
  <article class="blog-card" style="left:450px">
    <div class="photo" style="background:linear-gradient(135deg,#c9d3dc,#5c6672)" role="img" aria-label="Photo of a man reviewing charts on a laptop"></div>
    <div class="blog-date">Sep 15, 2022</div>
    <h3 class="blog-title">But I must explain to you how all this mistaken</h3>
    <p class="blog-text">At vero eos et accusamus et iusto odio dignissimos ducimus qui blanditiis praes entium voluptatum deleniti atque corrupti quos dolores et quas molestias</p>
    <a class="btn">Read More</a>
  </article>
  <article class="blog-card" style="left:769px">
    <div class="photo" style="background:linear-gradient(135deg,#3c4a5a,#7a6e62)" role="img" aria-label="Photo of business people with overlaid financial graphics"></div>
    <div class="blog-date">Sep 15, 2022</div>
    <h3 class="blog-title">At vero eos et accusamus et iusto odio dignissimos ducimus</h3>
    <p class="blog-text">At vero eos et accusamus et iusto odio dignissimos ducimus qui blanditiis praes entium voluptatum deleniti atque corrupti quos dolores et quas molestias</p>
    <a class="btn">Read More</a>
  </article>
</section>

<section class="cta" role="img" aria-label="Blue-tinted photo of a person working at a laptop">
  <h2 class="section-title" style="top:56px;color:var(--white);font-size:28px">Are you ready to get started?</h2>
  <p class="abs" style="left:0;top:122px;width:1200px;text-align:center;font-size:19px;line-height:29px;color:var(--white)">On the other hand, we denounce with righteous indignation and dislike<br>men who are so beguiled and demoralized by the charms</p>
  <a class="btn" style="left:525px;top:198px;width:148px;height:42px;font-size:14px">Get Started</a>
</section>

<footer class="site-footer">
  <div class="foot-col" style="left:130px"><h5>PRODUCTS</h5><a>Applicant Heron</a><a>Ledger Heron</a><a>Dwelling Heron</a></div>
  <div class="foot-col" style="left:278px"><h5>FEATURES</h5><a>Point of Sale</a><a>Communication</a><a>1003 Loan Application</a><a>Disclosure Desk</a></div>
  <div class="foot-col" style="left:473px"><h5>COMPANY</h5><a>Careers</a><a>Press Room</a><a>Legal</a></div>
  <div class="foot-col" style="left:639px"><h5>RESOURCES</h5><a>Webinars</a><a>Help Center</a><a>Free Trial</a><a>Schedule a Demo</a></div>
  <div class="wordmark" style="left:858px;top:42px;font-size:24px;color:var(--white)">Codeworks Heron</div>
  <div class="abs" style="left:921px;top:91px;font-family:'Montserrat',sans-serif;font-weight:700;font-size:11.5px">FOLLOW US</div>
  <div class="social"><span></span><span></span><span></span></div>
  <div class="abs" style="left:130px;top:200px;width:938px;height:1px;background:#3d3a40"></div>
  <div class="abs" style="left:0;top:237px;width:1200px;text-align:center;font-size:11.5px;color:#ddd">Copyright © 2022 All Rights Reserved</div>
</footer>

</body>
</html>
```